Web Design Project

Please take a look at my current aged website www.talvikhrconsulting.com and my newly designed logo and business cards. I would like a new fresh updated look to my website and my new designs incorporated.
Updates

  Good Morning Everyone

Due to an Austrralian licencing issue I have had to have my logo slightly redesigned.

Would you please be able to look at the newly uploaded files and revise your designs.

Thanks so much.  I am very happy with the calibre and quality of the designs so far.

kind Regards

Marla

Industry/Entity Type

Business

Requirements
Must have
• the exisiting pages and fresh new graphics and a real commitment to my palette of lime green, turqouise and black.

```html
<!DOCTYPE html>
<html lang="en">
<head>
<meta charset="utf-8">
<title>Talvik Consulting — Human Resources and Recruitment Solutions</title>
<link rel="stylesheet" href="https://fonts.googleapis.com/css2?family=Arimo:wght@400;700&family=Noto+Serif:wght@700&display=swap">
<style>
:root{
  --turquoise:#1ba3c6;
  --lime:#4cae3c;
  --ink:#111;
  --text:#7a7a7a;
  --text-dark:#666;
  --rule:#e2e2e2;
  --panel:#efefef;
  --footer-top:#dcdcdc;
  --white:#fff;
}
*{box-sizing:border-box;margin:0;padding:0}
html,body{width:818px;height:1200px;overflow:hidden;background:var(--white)}
body{position:relative;font-family:"Arimo",Arial,sans-serif;color:var(--text)}
.abs{position:absolute}
ul{list-style:none}

.account{left:653px;top:36px;font-size:11px;letter-spacing:.5px;color:var(--lime)}
.brand{left:57px;top:42px;display:flex;align-items:flex-end;gap:8px;height:84px}
.brand-dot{width:44px;height:44px;border-radius:50%;background:var(--turquoise);position:absolute;left:54px;top:0}
.brand-name{font-size:22px;font-weight:700;color:var(--turquoise);line-height:1;padding-bottom:2px}

.nav{left:330px;top:93px;width:428px;height:38px;border:1px solid #cfcfcf;border-radius:3px;
  background:linear-gradient(#fafafa,#dedede)}
.nav svg{position:absolute;left:0;top:0}
.nav a{position:absolute;top:12px;font-size:11px;font-weight:700;color:#888;text-decoration:none;letter-spacing:.2px}

.top-rule{left:57px;top:152px;width:702px;height:2px;background:#cfcfcf}
.slider{left:57px;top:155px;width:702px;height:344px;background:var(--panel)}
.slide-photo{left:201px;top:166px;width:417px;height:275px;
  background:radial-gradient(circle at 45% 40%,#e6f5fd 0%,#a9d8f2 55%,#7fc2ea 100%)}
.slide-shadow{left:195px;top:446px;width:430px;height:34px;border-radius:50%;
  background:radial-gradient(ellipse at center,rgba(0,0,0,.55) 0%,rgba(0,0,0,.25) 45%,rgba(0,0,0,0) 72%)}
.arrow{top:291px}

.col-title{font-family:"Noto Serif",Georgia,serif;font-weight:700;font-size:14px;color:var(--turquoise)}
.col-rule{height:3px;background:var(--rule)}
.plain-list li{font-size:10.5px;line-height:16px;color:var(--text)}
.bullet-list li{position:relative;font-size:10.5px;color:var(--lime);height:24px;padding:1px 0 0 15px}
.bullet-list li::before{content:"";position:absolute;left:0;top:3px;width:7px;height:7px;border:1.5px solid var(--turquoise);border-radius:50%}
.bullet-list li::after{content:"";position:absolute;left:7px;top:17px;width:146px;height:2px;background:var(--rule)}
.bullet-list li:first-child::after{width:197px}
.dev-list li{font-size:10.5px;font-weight:700;color:#8a8a8a;line-height:23px}
.fees-text{font-size:10.5px;line-height:11.5px;font-weight:700;color:#8a8a8a;letter-spacing:.2px}
.btn-more{left:682px;top:732px;width:57px;height:15px;border-radius:3px;background:var(--turquoise);
  color:var(--white);font-size:7.5px;font-weight:700;text-align:center;line-height:15px}

.divider{left:45px;top:782px;width:700px;height:8px;
  background:radial-gradient(ellipse at center top,rgba(0,0,0,.25) 0%,rgba(0,0,0,0) 70%)}
.intro-title{left:66px;top:809px;font-size:13.5px}
.intro-photo{left:66px;top:834px;width:138px;height:93px;background:linear-gradient(135deg,#6a4a36,#b9a48f 55,#e6e1d9)}
.intro-text{left:213px;top:836px;width:540px;font-size:12.3px;line-height:18.5px;color:#888}

.footer{left:0;top:949px;width:818px;height:251px;background:linear-gradient(var(--footer-top),var(--white))}
.foot-title{top:980px;font-size:13.5px}
.reach{left:66px;top:1010px;font-size:11px;line-height:15.7px;color:var(--text-dark)}
.quick{left:295px;top:1010px}
.quick li{font-size:11px;color:var(--text-dark);line-height:28px}
.mail-box{left:521px;top:981px;width:230px;height:156px;background:#d6d6d6}
.mail-title{left:531px;top:980px;font-size:18px;letter-spacing:1px}
.mail-text{left:524px;top:1010px;width:226px;font-size:11px;line-height:17px;font-weight:700;color:#8a8a8a;letter-spacing:.3px}
.mail-text b{color:var(--lime)}
.signup{left:536px;top:1107px;width:200px;height:26px;border-radius:13px;background:var(--white);
  border:1px solid #bbb;box-shadow:inset 0 1px 2px rgba(0,0,0,.2)}
.signup span{position:absolute;left:12px;top:7px;font-size:9.5px;font-weight:700;color:#777}
.signup b{position:absolute;right:-1px;top:-1px;width:44px;height:26px;border-radius:0 13px 13px 0;background:var(--turquoise);
  color:var(--white);font-size:8.5px;text-align:center;line-height:26px}
</style>
</head>
<body>

<div class="abs account">LOG IN | REGISTER</div>

<div class="abs brand"><span class="brand-name">Talvik Consulting</span></div>

<nav class="abs nav">
  <svg width="428" height="38" viewBox="0 0 428 38" aria-hidden="true">
    <g fill="none" stroke="#c4c4c4" stroke-width="1.2">
      <polyline points="70,0 88,19 70,38"/>
      <polyline points="166,0 184,19 166,38"/>
      <polyline points="270,0 288,19 270,38"/>
      <polyline points="352,0 370,19 352,38"/>
    </g>
  </svg>
  <a style="left:19px">HOME</a>
  <a style="left:99px">SERVICES</a>
  <a style="left:186px">COUSULTANT</a>
  <a style="left:279px">CONTACT US</a>
  <a style="left:371px">OUR FEE</a>
</nav>

<div class="abs top-rule"></div>
<div class="abs slider"></div>
<div class="abs slide-shadow"></div>
<div class="abs slide-photo" role="img" aria-label="Business handshake in front of a pale blue globe"></div>
<svg class="abs arrow" style="left:201px" width="26" height="26" viewBox="0 0 26 26" aria-label="Previous slide">
  <circle cx="13" cy="13" r="11.5" fill="#2b2b2b" stroke="#9fb4c4" stroke-width="2"/>
  <polygon points="16,7 8,13 16,19" fill="#fff"/>
</svg>
<svg class="abs arrow" style="left:591px" width="26" height="26" viewBox="0 0 26 26" aria-label="Next slide">
  <circle cx="13" cy="13" r="11.5" fill="#2b2b2b" stroke="#9fb4c4" stroke-width="2"/>
  <polygon points="10,7 18,13 10,19" fill="#fff"/>
</svg>

<!-- Service columns -->
<h2 class="abs col-title" style="left:66px;top:524px">People Systems and Processes</h2>
<div class="abs col-rule" style="left:66px;top:547px;width:191px"></div>
<ul class="abs plain-list" style="left:66px;top:561px;width:200px">
  <li>Attraction, Recruitment and Induction</li>
  <li>Remuneration, Benefits and Salary</li>
  <li>Talent Management and Retention</li>
  <li>Graduate Management</li>
  <li>Performance Management and Planning</li>
  <li>Conflict, Dispute and Grievance</li>
  <li>Facilitation and Resolution Workforce</li>
  <li>Planning.</li>
  <li>Reward and Recognition</li>
  <li>Leadership Programs</li>
  <li>Career Counselling</li>
  <li>Coaching and Mentoring</li>
</ul>

<h2 class="abs col-title" style="left:303px;top:524px">Employee Relations</h2>
<div class="abs col-rule" style="left:303px;top:547px;width:191px"></div>
<ul class="abs bullet-list" style="left:303px;top:564px">
  <li>HR Function Review and Assessments</li>
  <li>Industrial Relations advice</li>
  <li>Contracts of Employment</li>
  <li>Industrial Award Service</li>
  <li>Employee Entitlements</li>
  <li>Equal Opportunity</li>
  <li>Union issues</li>
  <li>Termination</li>
</ul>

<h2 class="abs col-title" style="left:530px;top:524px">Organisation Development</h2>
<div class="abs col-rule" style="left:530px;top:547px;width:184px"></div>
<ul class="abs dev-list" style="left:531px;top:558px">
  <li>Policy &amp; Procedure Development and Auditing</li>
  <li>Organisation Evaluation and Re-design</li>
  <li>Culture and Values Asssessment and Planning</li>
</ul>
<h2 class="abs col-title" style="left:530px;top:640px">Our Fees</h2>
<p class="abs fees-text" style="left:530px;top:666px;width:230px">Our highly competitive fees will be tailored to suit your organisation's individual needs Generally the Consultant's time will be charged at an hourly rate however some projects will require the Consultant :</p>
<div class="abs btn-more">view more &gt;&gt;</div>

<div class="abs divider"></div>

<h2 class="abs col-title intro-title">What can Talvik HR Consulting do for me?</h2>
<div class="abs intro-photo" role="img" aria-label="Business people meeting around a table with a laptop"></div>
<p class="abs intro-text">During these challenging economic times it can be difficult to justify internal human resources management services or support. However as a business owner or Manager you may find that HR support or advice is required from time to time. Talvik HR Consulting are an outsourced HR function.&nbsp; We can provide you with that ongoing support, offer solutions and assist you with developing strategies that fit your business and deliver results.</p>

<!-- Footer -->
<div class="abs footer"></div>

<h2 class="abs col-title foot-title" style="left:66px">How to reach us</h2>
<address class="abs reach" style="font-style:normal">
  148b Corrin Street<br>
  Westfield&nbsp; WA&nbsp; 6112<br>
  mobile<br>
  0412 555 730<br>
  email<br>
  marla@talvikHRconsulting.com<br>
  web<br>
  www.talvikHRconsulting.com
</address>

<h2 class="abs col-title foot-title" style="left:295px">Quick links</h2>
<ul class="abs quick">
  <li>Cousultant</li>
  <li>People System &amp; Processes</li>
  <li>Employee Relation</li>
  <li>Organisation Development</li>
  <li>Our Fee</li>
</ul>

<div class="abs mail-box"></div>
<h2 class="abs col-title mail-title">Join the mailing list</h2>
<p class="abs mail-text">User avoide filling out forms &amp; submiting their detail if possible. for a news latter sing-up, all&nbsp; you needis there <b>EMAIL</b> address</p>
<div class="abs signup"><span>Enter your EMAIL address</span><b>Sing up</b></div>

</body>
</html>
```